Dental Practice Billboard Design

We are a newer dental practice in need of a simple but appealing billboard for our growing dental practice to attract new patients. The practice is owned by husband and wife dentists and is family friendly in a small town in Kentucky. We try to be very friendly and caring to our patients. Would prefer a blue background for the billboard and our tooth logo to be prominent. We are partial to the Patua One font used in the image below but please feel free to tweak it as you deem necessary. The shape of the uppercase D and lowercase g are why we like that font, so fonts with a similarly shaped “D” and “g” would work as well. Please include our phone number (555) 847-1390. Please see our website Harlowbrookdentistry.example for more info on the practice if needed. Thank you! Looking forward to seeing your creation.
Updates

The dimensions will be 12ft x 24ft (3.6576m x 7.3152m). Apologies for not including this in the original prompt. Thank you all for your submissions.

Industry/Entity Type

Dental

Font styles to use
Other font styles liked:
• Patua One

Colors
0054AA
0677BA
7BADD7
CADEEF
E8F1F8
0094D4
00A9DD
6FCCEA
C7EBF8
E9F6FB
00AB8E
00BBA5
67D7C9
C6EFE9
E9F9F6
59FF00
82FF00
B8FF75
E3FFCB
F4FFEA

Requirements
Must have
• Phone number, website, Logo, Practice name “Harlow Brook Dentistry”
Should not have
• A tagline or slogan

```html
<!DOCTYPE html>
<html lang="en">
<head>
<meta charset="utf-8">
<title>Harlow Brook Dentistry — Billboard</title>
<link href="https://fonts.googleapis.com/css2?family=Patua+One&family=Nunito:wght@800;900&display=swap" rel="stylesheet">
<style>
  :root {
    --navy: #062a5c;
    --green: #1cb51c;
    --white: #ffffff;
    --stage: #e8eef5;
    --photo-warm: #c9a88c;
    --photo-light: #eef0f2;
  }
  * { margin: 0; padding: 0; box-sizing: border-box; }
  html, body { width: 1200px; height: 730px; overflow: hidden; background: var(--stage); }
  .billboard {
    position: absolute; left: 20px; top: 75px;
    width: 1160px; height: 580px;
    background: var(--navy);
    overflow: hidden;
  }
  .brand {
    position: absolute; left: 40px; top: 92px;
    display: flex; align-items: center; gap: 28px;
  }
  .brand-dot {
    width: 110px; height: 110px; border-radius: 50%;
    background: var(--green); flex: none;
  }
  .brand-name { font-family: "Patua One", serif; color: var(--white); line-height: 1; }
  .brand-name .primary { display: block; font-size: 86px; }
  .brand-name .secondary { display: block; font-size: 46px; margin-top: 8px; padding-left: 4px; }
  .divider {
    position: absolute; left: 0; top: 368px; width: 720px; height: 3px;
    background: linear-gradient(90deg, var(--green) 0%, var(--green) 55%, rgba(28,181,28,0) 100%);
  }
  .contact { position: absolute; left: 26px; top: 400px; color: var(--white); }
  .contact-row { display: flex; align-items: center; gap: 14px; }
  .contact-icon { width: 34px; height: 34px; flex: none; }
  .phone { font-family: "Nunito", sans-serif; font-weight: 900; font-size: 74px; letter-spacing: 1px; line-height: 1.05; }
  .website { font-family: "Patua One", serif; font-size: 36px; margin-top: 10px; }
  .website .tld { color: var(--green); }
  .team-photo {
    position: absolute; left: 780px; top: 40px; width: 340px; height: 500px;
    border-radius: 150px 150px 120px 120px;
    border: 14px solid var(--white);
    background: linear-gradient(160deg, var(--photo-light) 0%, var(--photo-warm) 55%, #ffffff 100%);
  }
  .team-photo-accent {
    position: absolute; left: 1085px; top: 20px; width: 46px; height: 46px;
    border-radius: 50%; background: var(--green);
  }
</style>
</head>
<body>
  <main class="billboard">
    <div class="brand">
      <span class="brand-dot"></span>
      <h1 class="brand-name">
        <span class="primary">Harlow Brook</span>
        <span class="secondary">Dentistry</span>
      </h1>
    </div>

    <div class="divider"></div>

    <div class="contact">
      <div class="contact-row">
        <svg class="contact-icon" viewBox="0 0 24 24" aria-hidden="true">
          <path fill="#1cb51c" d="M6.6 10.8c1.4 2.8 3.8 5.1 6.6 6.6l2.2-2.2c.3-.3.7-.4 1-.2 1.1.4 2.3.6 3.6.6.6 0 1 .4 1 1V20c0 .6-.4 1-1 1C10.6 21 3 13.4 3 4c0-.6.4-1 1-1h3.5c.6 0 1 .4 1 1 0 1.3.2 2.5.6 3.6.1.3 0 .7-.2 1L6.6 10.8z"/>
        </svg>
        <span class="phone">(555) 847-1390</span>
      </div>
      <div class="contact-row website">
        <svg class="contact-icon" viewBox="0 0 24 24" aria-hidden="true" fill="none" stroke="#1cb51c" stroke-width="1.8">
          <circle cx="12" cy="12" r="9.5"/>
          <ellipse cx="12" cy="12" rx="4.2" ry="9.5"/>
          <line x1="2.5" y1="12" x2="21.5" y2="12"/>
          <path d="M4.5 7h15M4.5 17h15"/>
        </svg>
        <span>Harlowbrookdentistry<span class="tld">.example</span></span>
      </div>
    </div>

    <div class="team-photo" role="img" aria-label="Photo of the two smiling dentists in white coats, standing side by side"></div>
    <span class="team-photo-accent"></span>
  </main>
</body>
</html>
```